Business Card Design needed - Something Awesome!

Need a business card designed. Company is "Marlowe Advisory" we do consulting and also have sales automation technology.
I'm going to use thick stock or metal, something really nice... I was thinking about a QR Code on the back that would just upload my contact info to the persons contact, etc -

This is a Strategy Company with a tech feel. I'm open to ideas but really want this to be nice!

I need a template that should include:

Name | Position or Title
D: 415.902.3376
www.marloweadvisory.example

I'm going to attach my contact so you can use that one, I need to get this printed.

Target Market(s)

Small to mid size customers, Entrepreneurs etc.

Industry/Entity Type

Consulting, Tech, Private Equity.

Contact Information for Business Card

Name, Phone, Maybe email, URL

Font styles to use
Sans Serif

Colors

Designer to choose only greyscale colors for use in the design.

Requirements
Must have
• Fresh, Clean, stand out from the crowd - will be on thick stock or metal.
Nice to have
• Clean, simple yet impactful.
Should not have
• Not cartoonish

```html
<!DOCTYPE html>
<html lang="en">
<head>
<meta charset="utf-8">
<title>Marlowe Advisory – Business Card</title>
<link rel="stylesheet" href="https://fonts.googleapis.com/css2?family=Inter:wght@400;500;700&display=swap">
<style>
  :root {
    --backdrop: #9b9b9b;
    --card: #141414;
    --ink: #ffffff;
    --ink-soft: #e6e6e6;
    --symbol-light: #f2f2f2;
    --symbol-mid: #8a8a8a;
  }
  * { margin: 0; padding: 0; box-sizing: border-box; }
  html, body {
    width: 1200px;
    height: 588px;
    overflow: hidden;
    background: var(--backdrop);
    font-family: "Inter", sans-serif;
  }
  .canvas {
    position: relative;
    width: 1200px;
    height: 588px;
  }
  .card {
    position: absolute;
    width: 486px;
    height: 287px;
    background: var(--card);
    color: var(--ink);
    overflow: hidden;
  }
  .card--front { left: 87px; top: 141px; }
  .card--back  { left: 622px; top: 143px; }

  .symbol-area {
    position: absolute;
    top: 0;
    height: 287px;
  }
  .card--front .symbol-area {
    left: 327px;
    width: 159px;
    background: linear-gradient(200deg, var(--symbol-light) 0%, var(--symbol-mid) 100%);
  }
  .card--back .symbol-area {
    left: 0;
    width: 159px;
    background: linear-gradient(160deg, var(--symbol-light) 0%, var(--symbol-mid) 100%);
  }

  .wordmark {
    position: absolute;
    font-weight: 500;
    color: var(--ink);
    line-height: 1;
    letter-spacing: 0.02em;
    white-space: nowrap;
  }
  .card--front .wordmark { left: 24px; top: 30px; font-size: 38px; }
  .card--back .wordmark  { left: 186px; top: 114px; font-size: 50px; }

  .identity-bar {
    position: absolute;
    left: 0;
    top: 123px;
    width: 9px;
    height: 34px;
    background: var(--ink);
  }
  .identity {
    position: absolute;
    left: 24px;
    top: 121px;
  }
  .identity__name {
    font-size: 16.5px;
    font-weight: 700;
    letter-spacing: 0.01em;
    line-height: 1.2;
  }
  .identity__title {
    font-size: 13px;
    font-weight: 400;
    color: var(--ink-soft);
    margin-top: 2px;
  }

  .contacts {
    position: absolute;
    left: 24px;
    top: 199px;
    list-style: none;
  }
  .contacts__item {
    display: flex;
    align-items: center;
    gap: 5px;
    font-size: 12.5px;
    color: var(--ink-soft);
    height: 19.5px;
    white-space: nowrap;
  }
  .contacts__icon {
    width: 11px;
    height: 11px;
    fill: var(--ink);
    flex: none;
  }
</style>
</head>
<body>
<main class="canvas">

  <section class="card card--front" aria-label="Card front">
    <div class="wordmark">MARLOWE</div>

    <span class="identity-bar"></span>
    <div class="identity">
      <p class="identity__name">DORIAN K. HALE</p>
      <p class="identity__title">Founder / CEO</p>
    </div>

    <ul class="contacts">
      <li class="contacts__item">
        <svg class="contacts__icon" viewBox="0 0 24 24" aria-hidden="true"><path d="M6.6 10.8c1.4 2.8 3.8 5.1 6.6 6.6l2.2-2.2c.3-.3.7-.4 1-.2 1.1.4 2.3.6 3.6.6.6 0 1 .4 1 1V20c0 .6-.4 1-1 1C10.6 21 3 13.4 3 4c0-.6.4-1 1-1h3.5c.6 0 1 .4 1 1 0 1.3.2 2.5.6 3.6.1.3 0 .7-.2 1l-2.3 2.2z"/></svg>
        415.902.3376
      </li>
      <li class="contacts__item">
        <svg class="contacts__icon" viewBox="0 0 24 24" aria-hidden="true"><path d="M2 5h20v2l-10 6L2 7z"/><path d="M2 9l10 6 10-6v10H2z"/></svg>
        info@marloweadvisory.example
      </li>
      <li class="contacts__item">
        <svg class="contacts__icon" viewBox="0 0 24 24" aria-hidden="true"><circle cx="12" cy="12" r="10" fill="none" stroke="#fff" stroke-width="2.4"/><path d="M7 6c2 1 3 3 2 5s1 3 0 5l-2 1M15 5c-1 2 1 3 2 4s2 0 3 1M14 14c1 1 3 1 3 3l-2 3" fill="none" stroke="#fff" stroke-width="2"/></svg>
        www.marloweadvisory.example
      </li>
    </ul>

    <div class="symbol-area" role="img" aria-label="Large brand symbol in white along the right edge"></div>
  </section>

  <section class="card card--back" aria-label="Card back">
    <div class="symbol-area" role="img" aria-label="Large brand symbol in white along the left edge"></div>
    <div class="wordmark">MARLOWE</div>
  </section>

</main>
</body>
</html>
```